Freelance business trainer needs a new business card

My business is called Brontlearn. I provide training in the workplace on management, coaching and mentoring, and customer service topics for a variety of businesses, colleges and private training providers, and teach on management programs. I need a professional but eye catching business card. Business colours grey and orange. My name Marion Tadwick; Tel 07382 415067; email mtadwick@brontlearn.co.uk; website www.brontlearn.co.uk.
Happy to have some sort of logo on front and details on back or all on one side
Target Market(s)
SME businesses and colleges - workshops i run are for adults in the workplace
Industry/Entity Type
Training
Look and feel

```html
<!DOCTYPE html>
<html lang="en">
<head>
<meta charset="utf-8">
<title>Brontlearn business card</title>
<link rel="stylesheet" href="https://fonts.googleapis.com/css2?family=Roboto+Condensed:wght@300;400;700&display=swap">
<style>
  :root {
    --orange: #f7901e;
    --orange-soft: #f9b468;
    --grey: #6d6e70;
    --grey-soft: #8a8b8d;
    --paper: #ffffff;
    --backdrop: #e9eaec;
  }
  * { margin: 0; padding: 0; box-sizing: border-box; }
  html, body {
    width: 1200px;
    height: 1000px;
    overflow: hidden;
    background: var(--backdrop);
    font-family: "Roboto Condensed", "Arial Narrow", sans-serif;
  }
  .sheet {
    position: relative;
    width: 1200px;
    height: 1000px;
    display: flex;
    align-items: center;
    justify-content: center;
    gap: 40px;
  }
  .card {
    position: relative;
    width: 500px;
    height: 300px;
    box-shadow: 0 6px 18px rgba(0,0,0,0.12);
    overflow: hidden;
  }

  /* Front: orange side */
  .card--front { background: var(--orange); }
  .card--front .website {
    position: absolute;
    left: 34px;
    top: 50%;
    transform: translateY(-50%);
    font-size: 26px;
    font-weight: 400;
    letter-spacing: 0.5px;
    color: var(--grey);
  }
  .card--front .divider {
    position: absolute;
    left: 292px;
    top: 42px;
    width: 1px;
    height: 216px;
    background: var(--grey-soft);
  }
  .card--front .emblem {
    position: absolute;
    left: 322px;
    top: 64px;
    width: 150px;
    height: 172px;
    border-radius: 48% 48% 22% 22%;
    background: radial-gradient(circle at 50% 40%, rgba(109,110,112,0.55), rgba(109,110,112,0.3));
  }

  /* Back: white side */
  .card--back { background: var(--paper); }
  .card--back .band {
    position: absolute;
    left: 0;
    bottom: 0;
    width: 100%;
    height: 24px;
    background: var(--orange);
  }
  .card--back .brand {
    position: absolute;
    left: 28px;
    top: 96px;
    font-size: 34px;
    font-weight: 700;
    color: var(--orange);
    letter-spacing: -0.5px;
  }
  .card--back .divider {
    position: absolute;
    left: 196px;
    top: 34px;
    width: 1px;
    height: 196px;
    background: var(--orange-soft);
  }
  .contacts {
    position: absolute;
    left: 220px;
    right: 36px;
    top: 66px;
    display: flex;
    flex-direction: column;
    gap: 28px;
  }
  .contact {
    display: flex;
    align-items: center;
    gap: 12px;
    color: var(--grey);
    font-size: 18px;
    font-weight: 400;
    white-space: nowrap;
  }
  .contact svg { flex: none; }
  .contact--phone .value { font-size: 21px; letter-spacing: 0.5px; }
</style>
</head>
<body>
  <main class="sheet">
    <section class="card card--front" aria-label="Card front">
      <p class="website">www.brontlearn.co.uk</p>
      <span class="divider"></span>
      <div class="emblem" role="img" aria-label="Grey line-drawn light bulb illustration"></div>
    </section>

    <section class="card card--back" aria-label="Card back">
      <p class="brand">Brontlearn</p>
      <span class="divider"></span>
      <div class="contacts">
        <div class="contact contact--phone">
          <svg width="32" height="32" viewBox="0 0 24 24" aria-hidden="true">
            <path fill="var(--orange)" d="M6.6 10.8a15.1 15.1 0 0 0 6.6 6.6l2.2-2.2c.3-.3.7-.4 1-.2 1.1.4 2.3.6 3.6.6.6 0 1 .4 1 1V20c0 .6-.4 1-1 1A17 17 0 0 1 3 4c0-.6.4-1 1-1h3.5c.6 0 1 .4 1 1 0 1.3.2 2.5.6 3.6.1.3 0 .7-.2 1l-2.3 2.2z"/>
          </svg>
          <span class="value">07382 415067</span>
        </div>
        <div class="contact contact--email">
          <svg width="32" height="24" viewBox="0 0 34 26" aria-hidden="true">
            <rect x="0" y="0" width="34" height="26" fill="var(--orange)"/>
            <path d="M1 1 L17 15 L33 1 M1 25 L13 12 M33 25 L21 12" fill="none" stroke="var(--paper)" stroke-width="2"/>
          </svg>
          <span class="value">mtadwick@brontlearn.co.uk</span>
        </div>
      </div>
      <span class="band"></span>
    </section>
  </main>
</body>
</html>
```